Road Construction Company needs business cards

We would like a new business card designed for our business.

We're a road construction company based in Qld, Australia.

Can the business card please have the following information on it.

Name: Warren Halbeck
Position: General Manager
Phone: 0472 915 348
Email: Warren.halbeck@tovrin.com.au
Address: 87 Marrow Ave, Pendlebay, QLD, 4023
Website: www.tovrin.com.au

Visually we'd like the card to be professional and simple.

Attached is our logo.

Our website is www.tovrin.com.au

Target Market(s)

Men aged 25-60

Contact Information for Business Card

As listed in project description

Font styles to use
Serif

Requirements
Must have
• Large logo on back of card

```html
<!DOCTYPE html>
<html lang="en">
<head>
<meta charset="utf-8">
<title>Tovrin – Business Card</title>
<link href="https://fonts.googleapis.com/css2?family=Montserrat:wght@400;600;700&display=swap" rel="stylesheet">
<style>
  :root {
    --backdrop: #dcdcdc;
    --card: #f4f4f4;
    --brand-blue: #0b4f9c;
    --band-start: #053a80;
    --band-end: #0b55a3;
    --text-grey: #555a60;
    --white: #ffffff;
  }
  * { box-sizing: border-box; margin: 0; padding: 0; }
  html, body {
    width: 1200px; height: 1200px; overflow: hidden;
    background: var(--backdrop);
    font-family: "Montserrat", Arial, sans-serif;
  }
  .card {
    position: absolute; left: 234px;
    width: 731px; height: 417px;
    background: var(--card);
  }
  .card--back { top: 160px; }
  .card--front { top: 632px; }

  .wordmark {
    position: absolute; left: 0; right: 0;
    text-align: center; color: var(--brand-blue);
    font-weight: 700; letter-spacing: 2px; text-transform: uppercase;
    line-height: 1;
  }
  .card--back .wordmark { top: 160px; font-size: 72px; }
  .card--front .wordmark { top: 48px; font-size: 48px; }

  .name-band {
    position: absolute; left: 0; right: 0; top: 159px; height: 97px;
    background: linear-gradient(90deg, var(--band-start), var(--band-end));
    color: var(--white); text-align: center;
  }
  .name-band .person { margin-top: 18px; font-size: 30px; font-weight: 600; line-height: 1.2; }
  .name-band .role { margin-top: 4px; font-size: 19px; font-weight: 400; }

  .contact-list {
    position: absolute; left: 54px; top: 284px; list-style: none;
    color: var(--text-grey); font-size: 19px; line-height: 28px;
  }
  .contact-list li { display: flex; align-items: center; gap: 10px; }
  .contact-list svg { width: 17px; height: 17px; fill: var(--brand-blue); flex: none; }

  .address {
    position: absolute; left: 479px; width: 220px; top: 284px;
    text-align: center; font-style: normal;
    color: var(--text-grey); font-size: 19px; line-height: 28px;
  }
</style>
</head>
<body>
  <section class="card card--back">
    <div class="wordmark">Tovrin</div>
  </section>

  <section class="card card--front">
    <div class="wordmark">Tovrin</div>

    <div class="name-band">
      <div class="person">Warren Halbeck</div>
      <div class="role">General Manager</div>
    </div>

    <ul class="contact-list">
      <li>
        <svg viewBox="0 0 24 24" aria-hidden="true"><path d="M6.6 10.8a15.2 15.2 0 0 0 6.6 6.6l2.2-2.2a1 1 0 0 1 1-.25 11.4 11.4 0 0 0 3.6.57 1 1 0 0 1 1 1V20a1 1 0 0 1-1 1A17 17 0 0 1 3 4a1 1 0 0 1 1-1h3.5a1 1 0 0 1 1 1c0 1.25.2 2.45.57 3.57a1 1 0 0 1-.25 1z"/></svg>
        0472 915 348
      </li>
      <li>
        <svg viewBox="0 0 24 24" aria-hidden="true"><path d="M2 5h20v14H2z M2 5l10 8 10-8" fill="var(--brand-blue)"/><path d="M3 6l9 7 9-7" fill="none" stroke="#fff" stroke-width="1.6"/></svg>
        Warren.halbeck@tovrin.com.au
      </li>
      <li>
        <svg viewBox="0 0 24 24" aria-hidden="true"><circle cx="12" cy="12" r="10"/><path d="M2 12h20M12 2c3 3 3 17 0 20M12 2c-3 3-3 17 0 20" fill="none" stroke="#fff" stroke-width="1.4"/></svg>
        www.tovrin.com.au
      </li>
    </ul>

    <address class="address">
      87 Marrow Ave,<br>
      Pendlebay,<br>
      QLD, 4023
    </address>
  </section>
</body>
</html>
```